Velvet Lantern rebranding my business with a new business card

I have my new logo and now I need a refresher on my business cards. I really want something fun and fresh. I like black background or anything to make the color pop.
Logo
Name: Velvet Lantern
Contact Info as stated below:
Mira Pellow
555-013-4762
Logo
Name: Velvet Lantern
Mira Pellow
555-013-4762
fb.me/VelvetLanternbyMira
Instagram: @VelvetLanternbyMira

Industry/Entity Type

Business

Contact Information for Business Card

double-sided. Logo on one side. Contact info on the other.

Requirements
Must have
• Logo
• Name: Velvet Lantern
• Contact Info as stated below:
• Mira Pellow
• 555-013-4762
• fb.me/VelvetLanternbyMira
• fb.me/VelvetLanternbyMira

```html
<!DOCTYPE html>
<html lang="en">
<head>
<meta charset="utf-8">
<title>Velvet Lantern – Business Card</title>
<link rel="stylesheet" href="https://fonts.googleapis.com/css2?family=Kurale&family=Raleway:wght@400;500&display=swap">
<style>
  :root {
    --stage: #0f0f0f;
    --card: #1d1d1d;
    --card-glow: #2a2a2a;
    --pink: #e98bc6;
    --cream: #efe8c8;
    --green: #7fc07f;
    --ghost: #262626;
    --icon-ink: #1d1d1d;
  }
  * { box-sizing: border-box; margin: 0; padding: 0; }
  html, body {
    width: 1200px; height: 1000px; overflow: hidden;
    background: var(--stage);
  }
  .stage {
    position: relative; width: 1200px; height: 1000px;
  }
  .card {
    position: absolute; top: 350px;
    width: 520px; height: 300px;
    border-radius: 18px; overflow: hidden;
    background: radial-gradient(ellipse at 50% 45%, var(--card-glow) 0%, var(--card) 70%);
    box-shadow: 0 10px 30px rgba(0,0,0,.6);
  }
  .card--front { left: 60px; }
  .card--back { left: 620px; }

  .ghost-name {
    position: absolute; left: 0; right: 0; top: 50%;
    transform: translateY(-50%);
    text-align: center;
    font-family: "Kurale", serif; font-size: 58px;
    color: var(--ghost); letter-spacing: 2px;
    white-space: nowrap;
  }

  .ring { position: absolute; inset: 0; }

  .brand-mark {
    position: absolute; left: 0; right: 0; top: 50%;
    transform: translateY(-50%);
    text-align: center;
    font-family: "Kurale", serif; font-size: 34px;
    color: var(--cream);
  }

  .contact-row {
    position: absolute; display: flex; align-items: center; gap: 10px;
    font-family: "Raleway", sans-serif; font-size: 14px; color: var(--green);
  }
  .contact-row--phone { left: 18px; top: 22px; right: 0; }
  .contact-row--social { left: 0; bottom: 56px; width: 440px; }
  .icon {
    flex: none; width: 22px; height: 22px; border-radius: 50%;
    background: var(--cream);
    display: flex; align-items: center; justify-content: center;
  }
  .dash {
    flex: 1; height: 0;
    border-top: 2px dashed var(--cream); opacity: .85;
  }
  .contact-row--phone .dash { margin-left: 6px; }
  .handle { font-size: 16px; }
  .icon--corner { position: absolute; right: 18px; bottom: 18px; }

  .person-name {
    position: absolute; left: 0; right: 0; top: 118px;
    text-align: center;
    font-family: "Kurale", serif; font-size: 44px; color: var(--pink);
  }
</style>
</head>
<body>
<main class="stage">

  <section class="card card--front" aria-label="Card front">
    <div class="ghost-name" aria-hidden="true">Velvet Lantern</div>
    <svg class="ring" viewBox="0 0 520 300" aria-hidden="true">
      <circle cx="260" cy="150" r="172" fill="none" stroke="var(--pink)" stroke-width="5"/>
      <circle cx="260" cy="150" r="160" fill="none" stroke="var(--pink)" stroke-width="2.5"/>
    </svg>
    <div class="brand-mark">Velvet Lantern</div>
  </section>

  <section class="card card--back" aria-label="Card back">
    <div class="ghost-name" aria-hidden="true">Velvet Lantern</div>

    <div class="contact-row contact-row--phone">
      <span class="icon" aria-hidden="true">
        <svg width="12" height="12" viewBox="0 0 24 24"><path fill="var(--icon-ink)" d="M6.6 10.8a15.1 15.1 0 0 0 6.6 6.6l2.2-2.2c.3-.3.7-.4 1-.2 1.1.4 2.3.6 3.6.6.6 0 1 .4 1 1V20c0 .6-.4 1-1 1A17 17 0 0 1 3 4c0-.6.4-1 1-1h3.5c.6 0 1 .4 1 1 0 1.3.2 2.5.6 3.6.1.3 0 .7-.2 1z"/></svg>
      </span>
      <span class="phone">555-013-4762</span>
      <span class="dash" aria-hidden="true"></span>
    </div>

    <h1 class="person-name">Mira Pellow</h1>

    <div class="contact-row contact-row--social">
      <span class="dash" aria-hidden="true"></span>
      <span class="icon" aria-hidden="true"></span>
      <span class="handle">VelvetLanternbyMira</span>
    </div>

    <span class="icon icon--corner" aria-hidden="true"></span>
  </section>

</main>
</body>
</html>
```